Probate (Legal) Wordpress Design with Coding for Online Company

I need a Wordpress design with coding, pictures, content to be provided by me, fully responsive, and development. This is for a 6-7 page design.

Pages Needed: Home/About/Probate/Process/FAQ/Contact Us/Blog.

The home page should be organized as followed:
-Steps in Probate: Gather; Implement; Close (each step will come with content)
-Flat-Fee Price & Savings: Content will go here with a button to contact us (phone number) or just the phone number.
-You Have Questions, We Have Answers: five questions with content. Only one question answer to show at a time when clicked on the question from the list.
-Get to Know Us: a brief description with content about what we do and who we are.

Main image slogan: Helping Californians deal with loss with DIGNITY & UNDERSTATING (you may use a better slogan if you wish).

The Contact page should not have a map since we are an online company. We service the entire state of California in every county and city.

The About page should be simple, direct, and easy on the eye. It should have a brief description of who we are and it should have no more than 6 reasons why the client should hire us.

About our online California company. We are not attorneys but legal document assistants who prepare legal documents for probate estate when someone dies with or without a will and assets need to be distributed. We have a flat-fee for Formal Probate of $999 and $699 for Informal Probate. We are an online company and offer our services to the entire state of California in every county. We do everything over the phone and email. The turn around time for us to prepare the initial legal paperwork for the client is within 3-5 business days. We can prepare, file, serve and manage a probate matter from petition to closing. We are not attorneys so our prices are very affordable compare to the attorney.

The company name for the website will be www.velmarhollow.com, The Velmar Hollow Group.

I do not have a logo yet. The colors of the website should be easy on the eye and calming. THE SITE SHOULD BE SIMPLE AND STRAIGHT TO THE POINT. EASY TO NAVIGATE.

The company phone number should be very visible and should stand out to the client. It should also be clickable and ready to dial for smartphone users.

I do not want a contact form on the homepage. THE MAIN THING IS FOR THE POTENTIAL CLIENT TO CALL OUR OFFICE TO SIGN UP.

I do like some images of family or people since we are dealing with people who just lost a loved one. Not all the images have to be of people.

The site should not look like we practice law or that people can mistake us for attorneys.

Target Market(s)

People who just lost a loved one who had property, assets, in California but died with or without a will or trust. This is for people looking to hire non-attorneys.

Coding

Coded - Design and coding required

Font styles to use
Serif

Colors

Designer to choose colors to be used in the design.

Requirements
Must have
• Refer to Project Description.
Nice to have
• The sample images provided is what I am attracted to for the homepage image.
Should not have

```html
<!DOCTYPE html>
<html lang="en">
<head>
<meta charset="utf-8">
<title>The Velmar Hollow Group — Probate Document Assistance</title>
<link href="https://fonts.googleapis.com/css2?family=PT+Serif:wght@400;700&family=Open+Sans:wght@400;600&display=swap" rel="stylesheet">
<style>
:root{
  --blue:#0b6dba;
  --blue-dark:#08579a;
  --olive:#a3ab2e;
  --logo-green:#3d7a2a;
  --ink:#1f1f1f;
  --text:#555;
  --steps-bg:#55585e;
  --faq-bg:#f2f2f2;
  --answer-bg:#eef0df;
  --answer-line:#c8cc9a;
  --footer-bg:#858c97;
  --white:#fff;
}
*{margin:0;padding:0;box-sizing:border-box}
html,body{width:1200px;height:3125px;overflow:hidden}
body{position:relative;background:var(--white);font-family:"Open Sans",Arial,sans-serif;color:var(--text)}
.serif{font-family:"PT Serif",Georgia,serif}
section,header,footer{position:absolute;left:0;width:1200px}
.abs{position:absolute}
.btn{position:absolute;width:170px;height:48px;background:var(--blue);color:var(--white);font:700 15px "PT Serif",Georgia,serif;text-transform:uppercase;display:flex;align-items:center;justify-content:center;border-bottom:3px solid var(--blue-dark);letter-spacing:.3px}

/* header */
.site-header{top:0;height:108px;background:var(--white)}
.brand{position:absolute;left:105px;top:38px;display:flex;align-items:center;gap:12px}
.brand-mark{width:30px;height:30px;background:var(--olive)}
.brand-name{font:700 24px "PT Serif",Georgia,serif;color:var(--logo-green);letter-spacing:.5px}
.phone-badge{position:absolute;left:787px;top:16px;width:153px;height:32px;background:var(--blue);border-radius:4px 16px 16px 4px;color:var(--white);font-size:13px;display:flex;align-items:center;padding-left:38px}
.phone-badge .ph{position:absolute;left:-2px;top:-2px;width:36px;height:36px;border-radius:50%;background:var(--white);border:2px solid var(--blue);display:flex;align-items:center;justify-content:center}
.socials{position:absolute;left:970px;top:16px;display:flex;gap:8px}
.socials span{width:27px;height:27px;border-radius:50%;background:#dfe3b5;border:2px solid #c9cf86}
.nav{position:absolute;top:74px;left:505px;display:flex;gap:0}
.nav a{font:700 15px "PT Serif",Georgia,serif;color:var(--ink);text-decoration:none;position:absolute;white-space:nowrap}
.nav a.active{color:var(--blue)}

/* hero */
.hero{top:108px;height:460px;background:linear-gradient(100deg,#6b5a48 0%,#8a8a62 35%,#9aa866 60%,#b8c48a 100%)}
.hero-copy{position:absolute;left:528px;top:134px;color:var(--white)}
.hero-copy .lead{font:700 29px "PT Serif",Georgia,serif}
.hero-copy .big{font:700 44px "PT Serif",Georgia,serif;margin-top:8px;letter-spacing:.5px}
.hero .btn{left:528px;top:260px;height:46px}
.dots{position:absolute;left:1075px;top:398px;display:flex;gap:4px}
.dots span{width:14px;height:14px;border-radius:50%;border:2px solid var(--white)}
.dots span.on{background:var(--white)}

/* steps */
.steps{top:568px;height:440px;background:linear-gradient(180deg,#4f5257,#5e6166 60%,#54575c)}
.section-title{font:700 34px "PT Serif",Georgia,serif;text-align:center;width:100%;position:absolute}
.steps .section-title{color:var(--white);top:66px}
.step{position:absolute;top:148px;width:250px;text-align:center;color:var(--white)}
.step .icon{width:90px;height:90px;border-radius:50%;background:var(--olive);margin:0 auto;display:flex;align-items:center;justify-content:center}
.step h3{font:400 22px "PT Serif",Georgia,serif;margin-top:18px}
.step p{font-size:14px;line-height:23px;margin-top:4px}
.chev{position:absolute;top:190px;color:#c7c9cc;font-size:30px;letter-spacing:-4px}

/* who */
.who{top:1008px;height:472px}
.who h2{position:absolute;left:104px;top:92px;font:700 34px "PT Serif",Georgia,serif;color:var(--ink)}
.who .copy{position:absolute;left:104px;top:152px;width:440px;font-size:14px;line-height:24px}
.who .copy p+p{margin-top:10px}
.who .btn{left:104px;top:322px}
.who .photo{position:absolute;left:583px;top:72px;width:514px;height:325px;background:linear-gradient(135deg,#d9dde3,#b9c2cf 50%,#6f7a8c);border:5px solid #eceef1}

/* flat fee */
.flatfee{top:1480px;height:480px;background:linear-gradient(180deg,#7e9aa8 0%,#9aa9ad 45%,#b59a7d 75%,#3a2a2a 100%)}
.flatfee h2{position:absolute;left:676px;top:98px;font:700 36px "PT Serif",Georgia,serif;color:var(--white)}
.flatfee p{position:absolute;left:676px;top:160px;width:445px;font-size:14px;line-height:24px;color:var(--white)}
.flatfee .btn{left:676px;top:327px}

/* what we do */
.services{top:1960px;height:380px}
.services .section-title{top:68px;color:var(--ink)}
.services .sub{position:absolute;top:126px;left:330px;width:540px;text-align:center;font-size:14px;line-height:24px}
.service{position:absolute;top:212px;width:200px;text-align:center}
.service .icon{height:60px;display:flex;align-items:center;justify-content:center}
.service h3{font:400 19px "PT Serif",Georgia,serif;color:var(--blue);margin-top:10px}

/* faq */
.faq{top:2340px;height:450px;background:var(--faq-bg)}
.faq .section-title{top:68px;color:var(--ink)}
.faq-list{position:absolute;left:104px;top:155px;width:496px}
.faq-item{height:36px;margin-bottom:6px;border:1px solid #cfcfcf;background:var(--white);font:700 15px "PT Serif",Georgia,serif;color:#333;display:flex;align-items:center;padding-left:34px;position:relative}
.faq-item.open{background:var(--blue);color:var(--white);border-color:var(--blue);padding-left:38px}
.faq-item.open::after{content:"";position:absolute;right:-28px;top:-1px;border-left:28px solid var(--blue);border-top:18px solid transparent;border-bottom:18px solid transparent}
.faq-answer{position:absolute;left:652px;top:153px;width:448px;height:220px;background:var(--answer-bg);border:1px solid var(--answer-line);padding:34px 26px;font-size:14px;line-height:24px}

/* footer */
.site-footer{top:2790px;height:335px;background:linear-gradient(180deg,#7d8591,#939aa5 50%,#8a919c);color:var(--white)}
.site-footer h4{font:700 19px "PT Serif",Georgia,serif;position:absolute;top:58px}
.foot-about{position:absolute;left:128px;top:102px;width:270px;font-size:13px;line-height:21px}
.foot-social{position:absolute;left:128px;top:178px;display:flex;gap:8px}
.foot-social span{width:24px;height:24px;border-radius:50%;background:rgba(255,255,255,.35);border:1px solid var(--white)}
.foot-links{position:absolute;left:560px;top:100px;list-style:none;font-size:13px;line-height:20px}
.foot-news{position:absolute;left:798px;top:100px;list-style:none;font-size:13px;line-height:30px}
.foot-news li::before{content:"» ";}
.foot-rule{position:absolute;left:96px;top:265px;width:1008px;height:1px;background:rgba(255,255,255,.4)}
.copyright{position:absolute;top:280px;width:100%;text-align:center;font-size:12px}
</style>
</head>
<body>

<header class="site-header">
  <div class="brand"><span class="brand-mark"></span><span class="brand-name">THE VELMAR HOLLOW GROUP</span></div>
  <div class="phone-badge"><span class="ph"><svg width="16" height="16" viewBox="0 0 24 24"><path d="M6.6 10.8a15 15 0 0 0 6.6 6.6l2.2-2.2a1 1 0 0 1 1-.25 11.4 11.4 0 0 0 3.6.6 1 1 0 0 1 1 1V20a1 1 0 0 1-1 1A17 17 0 0 1 3 4a1 1 0 0 1 1-1h3.5a1 1 0 0 1 1 1c0 1.25.2 2.45.6 3.6a1 1 0 0 1-.25 1z" fill="#0b6dba"/></svg></span>+1 800 555 0142</div>
  <div class="socials"><span></span><span></span><span></span><span></span></div>
  <nav class="nav">
    <a class="active" style="left:0">Home</a>
    <a style="left:85px">About</a>
    <a style="left:172px">Probate</a>
    <a style="left:272px">Process</a>
    <a style="left:368px">FAQ</a>
    <a style="left:442px">Contact Us</a>
    <a style="left:565px">Blog</a>
  </nav>
</header>

<section class="hero" role="img" aria-label="Photo of a young family with two small children sitting together on the grass in a sunny park">
  <div class="hero-copy">
    <div class="lead">Helping Californians deal with loss with</div>
    <div class="big">DIGNITY &amp; UNDERSTATING</div>
  </div>
  <a class="btn">Learn More</a>
  <div class="dots"><span class="on"></span><span></span><span></span></div>
</section>

<section class="steps" role="img" aria-label="Faded city skyline behind the probate steps">
  <h2 class="section-title">Steps In Probate</h2>
  <div class="step" style="left:91px">
    <div class="icon"><svg width="46" height="46" viewBox="0 0 46 46" fill="none" stroke="#fff" stroke-width="3" stroke-linecap="round"><path d="M5 5l13 13M18 10v8h-8M41 5L28 18M28 10v8h8M5 41l13-13M18 36v-8h-8M41 41L28 28M28 36v-8h8"/></svg></div>
    <h3>Gather</h3>
    <p>Lorem ipsum dolor sit amet, conectr adipiscing elit, sed do eiusmod tempor incididunt ut labore magna aliqua.</p>
  </div>
  <div class="chev" style="left:398px">››</div>
  <div class="step" style="left:431px">
    <div class="icon"><svg width="46" height="46" viewBox="0 0 46 46" fill="none" stroke="#fff" stroke-width="3" stroke-linecap="round"><path d="M8 38L34 12M14 32l-4-4M30 8l8 8M12 40l-6 0 0-6"/></svg></div>
    <h3>Implement</h3>
    <p>Lorem ipsum dolor sit amet, conectr adipiscing elit, sed do eiusmod tempor incididunt ut labore magna aliqua.</p>
  </div>
  <div class="chev" style="left:782px">››</div>
  <div class="step" style="left:860px">
    <div class="icon"><svg width="46" height="46" viewBox="0 0 46 46" fill="none" stroke="#fff" stroke-width="4" stroke-linecap="round"><path d="M23 6v16M14 11a14 14 0 1 0 18 0"/></svg></div>
    <h3>Close</h3>
    <p>Lorem ipsum dolor sit amet, conectr adipiscing elit, sed do eiusmod tempor incididunt ut labore magna aliqua.</p>
  </div>
</section>

<section class="who">
  <h2>Who We Are ?</h2>
  <div class="copy">
    <p>Lorem ipsum dolor sit amet, consectetur adipiscing elit, sed do eiusmod tempor incididunt ut labore et dolore magna aliqua.</p>
    <p>Duis aute irure dolor in reprehenderit in voluptate velit esse cillum dolore eu fugiat nulla pariatur. Excepteur sint occaecat cupidatat non proident, sunt in culpa qui officia deserunt mollit anim id est laborum.</p>
  </div>
  <a class="btn">Learn More</a>
  <div class="photo" role="img" aria-label="Photo of an older couple, a young woman and a smiling advisor reviewing papers at a table"></div>
</section>

<section class="flatfee" role="img" aria-label="Photo of a suspension bridge silhouetted against a dusky sky over hills">
  <h2>Flat-Fee Price &amp; Savings</h2>
  <p>Lorem ipsum dolor sit amet, consectetur adipiscing elit, sed do eiusmod tempor incididunt ut labore et dolore magna aliqua. Ut enim ad minim veniam, quis nostrud exercitation ullamco laboris nisi ut aliquip ex ea commodo consequat. Duis aute irure dolor in reprehenderit in voluptate velit esse cillum dolore eu fugiat nulla pariatur.</p>
  <a class="btn">Contact Us</a>
</section>

<section class="services">
  <h2 class="section-title">What We Do ?</h2>
  <p class="sub">Lorem ipsum dolor sit amet, consectetur adipiscing elit, sed do eiusmod tempor incididunt ut labore et dolore magna aliqua.</p>
  <div class="service" style="left:129px">
    <div class="icon"><svg width="52" height="44" viewBox="0 0 52 44"><rect x="18" y="2" width="16" height="8" fill="none" stroke="#a3ab2e" stroke-width="4"/><rect x="2" y="10" width="48" height="32" fill="#a3ab2e"/><rect x="2" y="22" width="48" height="3" fill="#fff"/></svg></div>
    <h3>Estate Planning</h3>
  </div>
  <div class="service" style="left:362px">
    <div class="icon"><svg width="56" height="50" viewBox="0 0 56 50" fill="#a3ab2e"><rect x="22" y="2" width="12" height="14"/><path d="M2 20l10 0 14 16 0 12-10 0zM54 20l-10 0-14 16 0 12 10 0z"/></svg></div>
    <h3>Diligence</h3>
  </div>
  <div class="service" style="left:642px">
    <div class="icon"><svg width="46" height="52" viewBox="0 0 46 52" fill="#a3ab2e"><circle cx="23" cy="13" r="11"/><path d="M2 52c0-16 9-24 21-24s21 8 21 24z"/></svg></div>
    <h3>Assistance</h3>
  </div>
  <div class="service" style="left:898px">
    <div class="icon"><svg width="44" height="56" viewBox="0 0 44 56"><rect x="2" y="2" width="40" height="52" fill="#a3ab2e"/><rect x="10" y="14" width="24" height="4" fill="#fff"/><rect x="6" y="46" width="32" height="3" fill="#fff"/></svg></div>
    <h3>Guidance</h3>
  </div>
</section>

<section class="faq">
  <h2 class="section-title">Frequently Asked Questions</h2>
  <div class="faq-list">
    <div class="faq-item open">Lorem ipsum dolor sit amet consectetur adipiscing elit ?</div>
    <div class="faq-item">Lorem ipsum dolor sit amet consectetur adipiscing elit ?</div>
    <div class="faq-item">Lorem ipsum dolor sit amet consectetur adipiscing elit ?</div>
    <div class="faq-item">Lorem ipsum dolor sit amet consectetur adipiscing elit ?</div>
    <div class="faq-item">Lorem ipsum dolor sit amet consectetur adipiscing elit ?</div>
  </div>
  <div class="faq-answer">Lorem ipsum dolor sit amet, consectetur adipiscing elit, sed do eiusmod tempor incididunt ut labore et dolore magna aliqua. Ut enim ad minim veniam, quis nostrud exercitation ullamco laboris nisi ut aliquip ex ea commodo consequat. Duis aute irure dolor in reprehenderit in voluptate velit esse cillum dolore eu fugiat nulla pariatur.</div>
</section>

<footer class="site-footer" role="img" aria-label="Faded waterfront city skyline behind the footer">
  <h4 style="left:128px">About Us</h4>
  <p class="foot-about">Lorem ipsum dolor sit amet, consectetur adipiscing elit, sed do eiusmod tempor incidi dunt ut labore et dolore magna aliqua.</p>
  <div class="foot-social"><span></span><span></span><span></span><span></span></div>
  <h4 style="left:560px">Links</h4>
  <ul class="foot-links"><li>Home</li><li>About</li><li>Probate</li><li>Process</li><li>FAQ</li><li>Contact Us</li><li>Blog</li></ul>
  <h4 style="left:798px">Recent News</h4>
  <ul class="foot-news">
    <li>Sed ut perspiciatis unde omnis iste</li>
    <li>Natus error sit voluptatem accusantium</li>
    <li>Doloremque laudantium, totam rem</li>
    <li>Aperiam, eaque ipsa quae ab illo</li>
  </ul>
  <div class="foot-rule"></div>
  <p class="copyright">Copyright © 2017 The Velmar Hollow Group - All Rights Reserved.</p>
</footer>

</body>
</html>
```